Drifting Tide Chronicle - Book Cover Design

I need a cover (front, spine, back) designed for the second edition of the historical book - Drifting Tide Chronicle. This book was created to be a more engaging supplementary resource to the dry texts of most middle and high school social studies classrooms. Although comprehensive and exhaustively researched, the book at times uses humor and irony to engage the reader. The cover should reflect this tone.

Book Title: Drifting Tide Chronicle
Subtitle: The Tales, Traditions and Turning Points of World History and the Regional Challenges of Today
Author: Owen Halvorsen
Updates

Project Deadline Extended
Reason: As multiple designers are working on adjustments and I am looking for new, creative ideas, I am extending the deadline five days. Thank you.

Project Deadline Extended
Reason: Artists are still making alterations to suggestions made and I also want to give designers a chance to submit new ideas.

Target Market(s)

Middle School and High School Teachers

Font styles to use
Serif

Colors
ec1f27
ffffff
000000

Requirements
Must have
• 1) See attachment for text for front cover, spine, back cover
• 2) Central, engaging image
Nice to have
• A subtle hint of humor, light tone
• Potentially upside down globe spinning
• Prefer black, red, white color scheme
Should not have
• Cartoonish text, images

```html
<!DOCTYPE html>
<html lang="en">
<head>
<meta charset="utf-8">
<title>Drifting Tide Chronicle – Book Cover</title>
<link rel="stylesheet" href="https://fonts.googleapis.com/css2?family=Alfa+Slab+One&family=Libre+Baskerville:wght@400;700&family=Open+Sans:ital,wght@0,400;0,700;1,400&display=swap">
<style>
  :root {
    --red: #ec1f27;
    --white: #ffffff;
    --black: #000000;
    --paper: #f7f6f3;
    --stage: #e6e6e6;
    --ink: #1a1a1a;
  }
  * { box-sizing: border-box; margin: 0; padding: 0; }
  html, body { width: 1200px; height: 1200px; overflow: hidden; }
  body { background: var(--stage); position: relative; font-family: "Open Sans", sans-serif; }

  .cover-wrap {
    position: absolute; left: 40px; top: 195px;
    width: 1120px; height: 810px;
    display: flex;
    box-shadow: 0 10px 30px rgba(0,0,0,0.18);
  }

  /* Back cover */
  .back-cover {
    width: 540px; height: 810px; background: var(--paper);
    padding: 46px 44px; color: var(--ink);
    font-size: 14.5px; line-height: 1.5; position: relative;
  }
  .back-cover .hook { font-weight: 700; font-size: 15.5px; margin-bottom: 16px; }
  .back-cover p { margin-bottom: 16px; text-align: justify; }
  .back-cover .endorsement { font-style: italic; font-size: 14px; }
  .back-cover .endorsement .attribution { font-style: normal; font-weight: 700; }

  /* Spine */
  .spine {
    width: 40px; height: 810px; background: var(--red);
    position: relative; color: var(--white);
  }
  .spine-title {
    position: absolute; left: 50%; top: 40px;
    writing-mode: vertical-rl; transform: translateX(-50%);
    font-family: "Libre Baskerville", serif; font-size: 21px;
    letter-spacing: 2px; text-transform: uppercase; white-space: nowrap;
  }
  .spine-credit {
    position: absolute; left: 50%; bottom: 28px;
    writing-mode: vertical-rl; transform: translateX(-50%);
    font-family: "Libre Baskerville", serif; font-size: 9.5px; line-height: 1.25;
    text-align: center; white-space: nowrap;
  }

  /* Front cover */
  .front-cover {
    width: 540px; height: 810px; background: var(--paper);
    position: relative; overflow: hidden;
  }
  .edition-tab {
    position: absolute; left: 177px; top: 0; width: 186px; height: 58px;
  }
  .edition-tab svg { position: absolute; inset: 0; }
  .edition-tab span {
    position: relative; display: block; text-align: center; padding-top: 14px;
    font-family: "Libre Baskerville", serif; font-weight: 700; font-size: 19px; color: var(--white);
  }
  .cover-illustration {
    position: absolute; left: 70px; top: 96px; width: 400px; height: 240px;
  }
  .title-block {
    position: absolute; left: 20px; right: 20px; top: 362px;
    text-align: center;
  }
  .book-title {
    font-family: "Alfa Slab One", serif; color: var(--red);
    font-size: 58px; line-height: 1.02; text-transform: uppercase;
    text-shadow: 3px 3px 0 rgba(0,0,0,0.25);
    font-weight: 400; letter-spacing: 0.5px;
  }
  .subtitle {
    font-family: "Libre Baskerville", serif; color: var(--ink);
    font-size: 18px; line-height: 1.3; margin-top: 22px;
  }
  .author {
    position: absolute; left: 0; right: 0; bottom: 58px; text-align: center;
    font-family: "Libre Baskerville", serif; font-size: 38px; color: var(--ink);
  }
</style>
</head>
<body>
  <main class="cover-wrap">
    <section class="back-cover">
      <p class="hook">Do you know how we got to here?</p>
      <p>Well, if you're like 97.4% of the people walking the planet, you haven't got a clue. Sure, you might know a bit about a couple rivers in Mesopotamia, how Theron wandered around Athens asking questions or how Matthias Lorne got ticked off one day and nailed a really long essay to the door of a church. But to be honest (and don't be embarrassed), you've got some gaps. Be dense no more. In <strong><em>Drifting Tide Chronicle</em></strong>, Owen Halvorsen once again takes you through all the major tales, traditions and turning points of world history &ndash; not just European history, but WORLD history. You'll figure out real quick that the West might have had some crowning moments, but for the whole of human history, it's been the Persians, the Indians, the Chinese, the Muslims or some horse peoples from the steppe that have truly turned us into the clever little creatures we are today.</p>
      <p>And while most world history books fade off once the Cold War comes to a close, this sometimes sardonic tome just gets going. Updated to include contemporary debates over topics such as Brexit, the rise of the Ashen Banner, claims to the South China Sea, the mounting refugee crisis and the controversial presidency of Dalton Marsh, this second edition finishes with a distinctively comprehensive look at the 21st century challenges facing nine major regions of today's world &ndash; Africa, Latin America, Japan, China, the Middle East, India, Russia, Europe and the United States.</p>
      <p class="endorsement">&ldquo;Owen Halvorsen expertly understands what his audience wants to know, what they need to know. A page-turning account of our proudest achievements and our most colossal bumblings. It's world history for the rest of us.&rdquo; &ndash; <span class="attribution">Idris Valmont</span></p>
    </section>

    <section class="spine">
      <div class="spine-title">Drifting Tide Chronicle</div>
      <div class="spine-credit">Owen Halvorsen<br>Second Edition</div>
    </section>

    <section class="front-cover">
      <div class="edition-tab">
        <svg width="186" height="58" viewBox="0 0 186 58" aria-hidden="true">
          <polygon points="0,0 186,0 186,46 93,58 0,46" fill="var(--ink)"/>
        </svg>
        <span>Second Edition</span>
      </div>

      <svg class="cover-illustration" viewBox="0 0 400 240" role="img" aria-label="Illustration: a grey and red hourglass standing on a red world map">
        <defs>
          <linearGradient id="illustration-tone" x1="0" y1="0" x2="0" y2="1">
            <stop offset="0" stop-color="#c4c4c4"/>
            <stop offset="0.45" stop-color="#dc6b6e"/>
            <stop offset="1" stop-color="#ec1f27"/>
          </linearGradient>
        </defs>
        <rect x="0" y="0" width="400" height="240" rx="14" fill="url(#illustration-tone)" opacity="0.85"/>
      </svg>

      <div class="title-block">
        <h1 class="book-title">Drifting<br>Tide<br>Chronicle</h1>
        <p class="subtitle">The tales, traditions and turning points<br>of world history<br>and the regional challenges of today.</p>
      </div>

      <p class="author">Owen Halvorsen</p>
    </section>
  </main>
</body>
</html>
```